Kessara Investment Brochure for investment promotion

We need an investment manual to sell the potential of Kessara state (a state in Nigeria) to investors around the world. This manual / brochure should be top class and have a premium feel.

We have developed the content as attached and all that is required is to fit the content into a brochure format.
The brochure should be top class, easy to read and very friendly to investors

Target Market(s)

World Investors

Industry/Entity Type

Investment

Requirements
Must have
• Kessara State Logo (Can find online), Kessara Tower (can find online). Premium feel and look. design should be clean, no clutter. General images that represent investment sectors
Nice to have
• Pictures
Should not have
• Images of white men.

```html
<!DOCTYPE html>
<html lang="en">
<head>
<meta charset="utf-8">
<title>Industry Overview / Investment Opportunities</title>
<link href="https://fonts.googleapis.com/css2?family=Open+Sans:wght@400;600;700&display=swap" rel="stylesheet">
<style>
  :root {
    --band-green: #2f6a2b;
    --heading-green: #3d7f22;
    --sub-green: #4a8a2a;
    --text: #2b2b2b;
    --paper: #ffffff;
    --photo-dark: #3a2a22;
    --photo-mid: #7a5a44;
    --photo-light: #c9b29a;
  }
  * { box-sizing: border-box; margin: 0; padding: 0; }
  html, body { width: 849px; height: 1200px; overflow: hidden; background: var(--paper); }
  body { font-family: "Open Sans", Arial, sans-serif; color: var(--text); position: relative; }
  .page-band {
    height: 40px; background: var(--band-green);
    display: flex; align-items: center; padding-left: 22px;
  }
  .page-title { color: #fff; font-weight: 400; font-size: 21px; letter-spacing: .2px; }
  .content { padding: 14px 26px 0 26px; font-size: 10.6px; line-height: 15.5px; }
  .section-title { color: var(--heading-green); font-weight: 700; font-size: 13.5px; margin: 4px 0 6px; }
  .sub-title { color: var(--sub-green); font-weight: 700; font-size: 10.8px; margin-top: 7px; }
  p { margin-bottom: 8px; }
  .sub-title + p { margin-bottom: 2px; }
  .area-list { list-style: none; margin: 0 0 26px; }
  .area-list li { position: relative; padding-left: 22px; margin-bottom: 2.5px; }
  .area-list li::before { content: "•"; position: absolute; left: 2px; }
  .energy { margin-top: 6px; }
  .feature-photo {
    position: absolute; left: 24px; right: 16px; top: 884px; bottom: 0;
    background: linear-gradient(160deg, var(--photo-light) 0%, var(--photo-mid) 40%, var(--photo-dark) 100%);
  }
</style>
</head>
<body>
  <header class="page-band">
    <h1 class="page-title">Industry Overview / Investment Opportunities</h1>
  </header>

  <main class="content">
    <section class="education">
      <h2 class="section-title">Education</h2>
      <p>The Education sector is a key priority of the State Government hence huge opportunities exist for investors in this important sector both in the provision of education and management of educational facilities.</p>
      <p>Investment areas include but not limited to:</p>
      <ul class="area-list">
        <li>Development of specialized training facilities</li>
        <li>Building and Management of model schools</li>
        <li>Development of Technology, Science, ICT and Technical institutions</li>
        <li>Development and management of technical and vocational centres and institutions</li>
        <li>Management of State-owned schools</li>
        <li>Provision of modern school equipment</li>
      </ul>
    </section>

    <section class="energy">
      <h2 class="section-title">Energy</h2>
      <p>Kessara is blessed with sizeable Crude Oil &amp; Gas deposits and is a member of the Niger Delta Oil producing zone, which accounts for about 70% of Nigeria’s total foreign exchange earnings.</p>
      <p>However, despite the large foreign direct investment in the energy sector, the state’s vast gas reserves are barely tapped but flared and wasted. If properly harnessed, this could become a great revenue earner for the state.</p>
      <p>The government is thus looking for private partnerships to tap into this largely untapped sector.</p>
      <p>A Power Master Plan is currently being conceptualized to address the generation, distribution, transmission and marketing challenges, and highlight specific opportunities for private sector participation.</p>
      <p>The Government is committed to stimulating investment in the sector, and ready to partner with investors to that effect.</p>
      <p>There are ample opportunities in the following areas:</p>

      <h3 class="sub-title">Power Generation</h3>
      <p>Given the gas reserves of the state, there are huge opportunities to develop gas-fired power plants.</p>

      <h3 class="sub-title">Power Distribution</h3>
      <p>Power distribution also holds huge potential for investors in the state, the distribution network requires upgrading and substantial investment, and private sector participation is crucial.</p>

      <h3 class="sub-title">Renewable Energy</h3>
      <p>Development of renewable energy is also an investment area requiring private participation especially for rural electrification. Waste-to-energy, solar and wind energy are under special considerations.</p>
    </section>
  </main>

  <div class="feature-photo" role="img" aria-label="Photograph of smiling schoolchildren in a classroom"></div>
</body>
</html>
```